Electric mountain bike tours nz

We are an Electric Mountain bike tour company in New Zealand. We will be offering bike rental and guided tours around the Nelson region in New Zealand. I want our website to represent both Mountain biking and New Zealand with the colours layout and features. We want tabs for the following:
-1 about us
-2 what we offer
-3 bookings/contact
Under the about us tab will be who we are as a a company. I want the ability to add videos to each of these tabs as we move foward with videos of the tracks we will be riding. I want the website to be editable so I can add and remove videos/photos myself. Also "our bikes" will be under this tab.
Under the what we offer tab will be
-1 bike rental and pricing
-2 guided tours and pricing
-3 recommended package deals.
I want to able to put the tracks under the guided tours tab and select beginner/ intermediate/advanced and have the tracks in each of the following to match the rider level. Also to be able to have a small video of the track would be great in this section.
Bookings and contact tab
(Further information for this tab to be updated soon)
Coded - Design and coding required
1 page
- Silver ferns, kiwi, mountains

```html
<!DOCTYPE html>
<html lang="en">
<head>
<meta charset="utf-8">
<title>Tasman E-Ride — Electric Mountain Bike Tours</title>
<link href="https://fonts.googleapis.com/css2?family=Lato:wght@400;700;900&display=swap" rel="stylesheet">
<style>
:root{
  --black:#000;
  --white:#fff;
  --ink:#111;
  --muted:#555;
  --accent-grey:#a9a9a9;
  --panel-1:#efefef;
  --panel-2:#dcdcdc;
  --panel-3:#bdbdbd;
  --footer-bar:#3a3a3a;
  --line:#777;
}
*{box-sizing:border-box;margin:0;padding:0}
html,body{width:1200px;height:2769px;overflow:hidden}
body{font-family:'Lato',Arial,sans-serif;color:var(--ink);background:var(--white);position:relative}
.bolt{display:inline-block;vertical-align:middle}

/* Header */
.site-header{position:absolute;left:0;top:0;width:1200px;height:150px;background:var(--black);color:var(--white)}
.brand{position:absolute;left:88px;top:58px;display:flex;align-items:center;gap:10px;font-weight:900;font-size:22px;color:var(--white)}
.brand-dot{width:24px;height:24px;border-radius:50%;background:var(--white)}
.main-nav{position:absolute;left:550px;top:68px;display:flex;align-items:center;gap:20px;font-size:14px;font-weight:700}
.main-nav a{color:var(--white);text-decoration:none}
.social{position:absolute;left:1006px;top:68px;display:flex;gap:6px}
.social span{width:17px;height:17px;border-radius:50%;background:var(--white)}

/* Hero */
.hero{position:absolute;left:0;top:150px;width:1200px;height:670px;
  background:linear-gradient(180deg,#3d5a78 0%,#6a7f93 35%,#8a7a64 58%,#3a3124 78%,#1b160f 100%)}
.hero-photo{position:absolute;inset:0}
.hero-title{position:absolute;left:461px;top:285px;width:660px;font-size:56px;font-weight:900;color:var(--white);letter-spacing:1px}
.hero-text{position:absolute;left:470px;top:357px;width:640px;text-align:center;font-size:14px;line-height:22px;color:#eee}
.btn{position:absolute;display:flex;align-items:center;justify-content:center;font-weight:700;font-size:15px;text-decoration:none}
.btn .bolt{position:absolute;left:-8px;top:-6px}
.btn-light{border:2px solid var(--white);color:var(--white)}
.btn-dark{border:2px solid var(--ink);color:var(--ink)}
.hero .btn{left:705px;top:437px;width:159px;height:41px}

/* Section headings */
.section-title{font-size:28px;font-weight:700}
.section-title em{font-style:normal;color:var(--accent-grey)}

/* About */
.about{position:absolute;left:0;top:820px;width:1200px;height:467px}
.about .section-title{position:absolute;left:90px;top:80px}
.about-text{position:absolute;left:90px;top:132px;width:554px;font-size:14px;line-height:22px;color:var(--muted);text-align:justify}
.about .btn{left:90px;top:336px;width:152px;height:38px}
.video{position:absolute;left:718px;top:136px;width:395px;height:238px;background:linear-gradient(160deg,#5b7fa8,#d9e4ef 55%,#243447);overflow:hidden}
.video-play{position:absolute;left:176px;top:90px;width:40px;height:40px;border-radius:50%;background:rgba(255,255,255,.9)}
.video-bar{position:absolute;left:0;bottom:0;width:100%;height:28px;background:#1b2836}
.video-track{position:absolute;left:62px;top:12px;width:320px;height:4px;background:#ddd}
.video-progress{position:absolute;left:0;top:0;width:120px;height:4px;background:#d11}

/* Our bikes */
.bikes{position:absolute;left:0;top:1287px;width:1200px;height:354px;background:linear-gradient(180deg,#5b5a4a,#6f6e66 50%,#4a4a48)}
.bikes-bg{position:absolute;inset:0}
.bikes .section-title{position:absolute;left:0;top:36px;width:1200px;text-align:center;color:var(--white)}
.bike-photo{position:absolute;left:144px;top:101px;width:426px;height:203px;background:linear-gradient(180deg,#9bb07a,#8a8a7a 55%,#6f6f6c)}
.bikes-text{position:absolute;left:611px;top:100px;width:470px;font-size:14px;line-height:22px;color:var(--white)}
.bikes .btn{left:611px;top:262px;width:151px;height:40px}

/* Offer */
.offer{position:absolute;left:0;top:1641px;width:1200px;height:676px}
.offer .section-title{position:absolute;left:0;top:64px;width:1200px;text-align:center}
.offer-col{position:absolute;top:141px;width:343px}
.offer-col h3{font-size:22px;font-weight:700;height:55px}
.offer-panel{height:480px;padding-top:0}
.col-1{left:85px}.col-1 .offer-panel{background:var(--panel-1)}
.col-2{left:428px}.col-2 .offer-panel{background:var(--panel-2)}
.col-3{left:772px;width:344px}.col-3 .offer-panel{background:var(--panel-3)}
.offer-item{position:relative;height:140px}
.offer-thumb{position:absolute;left:0;top:0;width:116px;height:116px}
.offer-body{position:absolute;left:135px;top:2px;width:190px}
.offer-body h4{font-size:15px;font-weight:700;margin-bottom:8px}
.offer-body p{font-size:11.5px;line-height:14px;color:var(--muted);text-align:justify}
.offer-body a{display:block;margin-top:9px;font-size:11.5px;font-weight:700;color:var(--ink);text-decoration:none}
.t1{background:linear-gradient(180deg,#6a8fb5,#4a5e3a)}
.t2{background:linear-gradient(180deg,#8fb3e0,#6f9a48)}
.t3{background:linear-gradient(180deg,#e6e6e6,#b79a6a)}
.t4{background:linear-gradient(180deg,#7a5a2e,#2f2a1c)}
.t5{background:linear-gradient(180deg,#cfd6dc,#5a5550)}
.t6{background:linear-gradient(180deg,#3a5e4a,#5a3a2a)}
.t7{background:linear-gradient(180deg,#9fb0c0,#6f7a48)}
.t8{background:linear-gradient(180deg,#eaeaea,#4a4440)}
.t9{background:linear-gradient(180deg,#6a8a5a,#8aa86a)}

/* Footer */
.site-footer{position:absolute;left:0;top:2317px;width:1200px;height:397px;background:var(--black);color:var(--white)}
.footer-brand{position:absolute;left:114px;top:90px;width:170px;display:flex;align-items:center;gap:10px;font-size:22px;font-weight:900}
.footer-brand .brand-dot{width:24px;height:24px}
.follow{position:absolute;left:122px;top:268px;width:200px;font-size:16px;font-weight:900;padding-bottom:10px;border-bottom:1px dotted var(--line)}
.follow em{font-style:normal}
.site-footer .social{left:122px;top:320px}
.footer-col h5{font-size:20px;font-weight:400;padding-bottom:10px;border-bottom:1px dotted var(--line);width:198px}
.contact{position:absolute;left:377px;top:55px}
.contact address{font-style:normal;font-size:12px;line-height:16px;margin:18px 0 14px}
.contact ul{list-style:none;font-size:12px;line-height:22px}
.contact ul svg{vertical-align:middle;margin-right:6px}
.quicklinks{margin-top:22px}
.quicklinks ul{list-style:none;font-size:12px;line-height:22px;margin-top:12px}
.quicklinks li::before{content:"‹";margin:0 10px 0 2px}
.booking{position:absolute;left:650px;top:55px;width:440px}
.booking h5{border:none;width:auto;font-size:20px}
.field{position:absolute;border:1px solid #bbb;height:33px;font-size:12px;padding:8px 6px;color:var(--white)}
.f1{left:0;top:52px;width:214px}.f2{left:221px;top:52px;width:214px}
.f3{left:0;top:96px;width:214px}.f4{left:221px;top:96px;width:214px}
.f5{left:0;top:139px;width:435px;height:86px}
.submit{position:absolute;left:0;top:258px;width:118px;height:28px;background:#b3b3b3;color:var(--white);font-size:14px;display:flex;align-items:center;justify-content:center}
.footer-bar{position:absolute;left:0;top:2714px;width:1200px;height:55px;background:var(--footer-bar);color:#ccc;font-size:14px;display:flex;align-items:center;justify-content:center;gap:10px}
</style>
</head>
<body>

<header class="site-header">
  <div class="brand"><span class="brand-dot"></span>Tasman E-Ride</div>
  <nav class="main-nav">
    <a href="#about">About us</a>
    <svg class="bolt" width="12" height="16" viewBox="0 0 12 16"><polygon points="7,0 0,9 5,9 3,16 12,6 7,6 9,0" fill="#fff"/></svg>
    <a href="#offer">What we offer</a>
    <svg class="bolt" width="12" height="16" viewBox="0 0 12 16"><polygon points="7,0 0,9 5,9 3,16 12,6 7,6 9,0" fill="#fff"/></svg>
    <a href="#booking">Bookings/Contact</a>
  </nav>
  <div class="social" aria-label="Social links"><span></span><span></span><span></span><span></span><span></span></div>
</header>

<section class="hero">
  <div class="hero-photo" role="img" aria-label="Mountain biker riding up a grassy hillside at sunset under a cloudy sky"></div>
  <h1 class="hero-title">LOREM IPSUM DOLOR</h1>
  <p class="hero-text">We are an Electric Mountain bike tour company in New Zealand. We will be offering bike rental and guided tours around the Nelson region in New Zealand.</p>
  <a class="btn btn-light" href="#booking">
    <svg class="bolt" width="20" height="34" viewBox="0 0 12 20"><polygon points="8,0 0,11 5,11 3,20 12,7 7,7 10,0" fill="#fff"/></svg>BOOK NOW</a>
</section>

<section class="about" id="about">
  <h2 class="section-title">About <em>Us</em></h2>
  <p class="about-text">Lorem ipsum dolor sit amet, consectetuer adipiscing elit. Aenean commodo ligula eget dolor. Aenean massa. Cum sociis natoque penatibus et magnis dis parturient montes, nascetur ridiculus mus. Donec quam felis, ultricies nec, pellentesque eu, pretium quis, sem. Nulla consequat massa quis enim. Donec pede justo, fringilla vel, aliquet nec, vulputate eget, arcu. In enim justo, rhoncus ut, imperdiet a, venenatis vitae, justo. Nullam dictum felis eu pede mollis pretium. Integer tincidunt. Cras dapibus. Vivamus elementum semper nisi.</p>
  <a class="btn btn-dark" href="#about">
    <svg class="bolt" width="20" height="34" viewBox="0 0 12 20"><polygon points="8,0 0,11 5,11 3,20 12,7 7,7 10,0" fill="#888"/></svg>Read More</a>
  <div class="video">
    <div role="img" aria-label="Rider's view from the handlebars on a snowy forest trail" style="position:absolute;inset:0"></div>
    <div class="video-play"><svg width="40" height="40" viewBox="0 0 40 40"><polygon points="16,12 28,20 16,28" fill="#111"/></svg></div>
    <div class="video-bar">
      <svg style="position:absolute;left:10px;top:8px" width="34" height="12" viewBox="0 0 34 12"><polygon points="0,0 9,6 0,12" fill="#fff"/><rect x="18" y="0" width="4" height="12" fill="#fff"/><rect x="25" y="0" width="4" height="12" fill="#fff"/></svg>
      <div class="video-track"><div class="video-progress"></div></div>
    </div>
  </div>
</section>

<section class="bikes">
  <div class="bikes-bg" role="img" aria-label="Winding mountain road through dry hills"></div>
  <h2 class="section-title">Our <em>Bikes</em></h2>
  <div class="bike-photo" role="img" aria-label="Electric mountain bike parked on a roadside"></div>
  <p class="bikes-text">Lorem ipsum dolor sit amet, consectetuer adipiscing elit. Aenean commodo ligula eget dolor. Aenean massa. Cum sociis natoque penatibus et magnis dis parturient montes, nascetur ridiculus mus. Donec quam felis, ultricies nec, pellentesque eu, pretium quis, sem. Nulla consequat massa quis enim. Donec pede justo, fringilla vel, aliquet nec, vulputate eget, arcu.</p>
  <a class="btn btn-light" href="#about">
    <svg class="bolt" width="20" height="34" viewBox="0 0 12 20"><polygon points="8,0 0,11 5,11 3,20 12,7 7,7 10,0" fill="#ccc"/></svg>Read More</a>
</section>

<section class="offer" id="offer">
  <h2 class="section-title">What we <em>Offer</em></h2>

  <div class="offer-col col-1">
    <h3>Bike rental &amp; pricing</h3>
    <div class="offer-panel">
      <div class="offer-item"><div class="offer-thumb t1" role="img" aria-label="Rider overlooking a mountain valley"></div><div class="offer-body"><h4>Lorem ipsum dolor</h4><p>Lorem ipsum dolor sit amet, consectetur adipiscing elit. Quid autem habent admirationis, cum prope accesseris?</p><a href="#">Read more &nbsp;»</a></div></div>
      <div class="offer-item"><div class="offer-thumb t2" role="img" aria-label="Rider on a green hillside trail"></div><div class="offer-body"><h4>Lorem ipsum dolor</h4><p>Lorem ipsum dolor sit amet, consectetur adipiscing elit. Quid autem habent admirationis, cum prope accesseris?</p><a href="#">Read more &nbsp;»</a></div></div>
      <div class="offer-item"><div class="offer-thumb t3" role="img" aria-label="Rider on a track near wind turbines"></div><div class="offer-body"><h4>Lorem ipsum dolor</h4><p>Lorem ipsum dolor sit amet, consectetur adipiscing elit. Quid autem habent admirationis, cum prope accesseris?</p><a href="#">Read more &nbsp;»</a></div></div>
    </div>
  </div>

  <div class="offer-col col-2">
    <h3>Guided tours &amp; pricing</h3>
    <div class="offer-panel">
      <div class="offer-item"><div class="offer-thumb t4" role="img" aria-label="Rider on a forest trail"></div><div class="offer-body"><h4>Beginner</h4><p>Lorem ipsum dolor sit amet, consectetur adipiscing elit. Quid autem habent admirationis, cum prope accesseris?</p><a href="#">Read more &nbsp;»</a></div></div>
      <div class="offer-item"><div class="offer-thumb t5" role="img" aria-label="Group of riders with their bikes"></div><div class="offer-body"><h4>Intermediate</h4><p>Lorem ipsum dolor sit amet, consectetur adipiscing elit. Quid autem habent admirationis, cum prope accesseris?</p><a href="#">Read more &nbsp;»</a></div></div>
      <div class="offer-item"><div class="offer-thumb t6" role="img" aria-label="Rider descending a steep trail"></div><div class="offer-body"><h4>Advanced</h4><p>Lorem ipsum dolor sit amet, consectetur adipiscing elit. Quid autem habent admirationis, cum prope accesseris?</p><a href="#">Read more &nbsp;»</a></div></div>
    </div>
  </div>

  <div class="offer-col col-3">
    <h3>Recommended package deals</h3>
    <div class="offer-panel">
      <div class="offer-item"><div class="offer-thumb t7" role="img" aria-label="Riders crossing open hill country"></div><div class="offer-body"><h4>Lorem ipsum dolor</h4><p>Lorem ipsum dolor sit amet, consectetur adipiscing elit. Quid autem habent admirationis, cum prope accesseris?</p><a href="#">Read more &nbsp;»</a></div></div>
      <div class="offer-item"><div class="offer-thumb t8" role="img" aria-label="Group of riders on a ridge"></div><div class="offer-body"><h4>Lorem ipsum dolor</h4><p>Lorem ipsum dolor sit amet, consectetur adipiscing elit. Quid autem habent admirationis, cum prope accesseris?</p><a href="#">Read more &nbsp;»</a></div></div>
      <div class="offer-item"><div class="offer-thumb t9" role="img" aria-label="Riders on a grassy path"></div><div class="offer-body"><h4>Lorem ipsum dolor</h4><p>Lorem ipsum dolor sit amet, consectetur adipiscing elit. Quid autem habent admirationis, cum prope accesseris?</p><a href="#">Read more &nbsp;»</a></div></div>
    </div>
  </div>
</section>

<footer class="site-footer" id="booking">
  <div class="footer-brand"><span class="brand-dot"></span>Tasman E-Ride</div>
  <p class="follow">FOLLOW US <em>ON</em></p>
  <div class="social" aria-label="Social links"><span></span><span></span><span></span><span></span><span></span></div>

  <div class="footer-col contact">
    <h5>Contact</h5>
    <address>42 Harbour Road<br>Nelson 7010</address>
    <ul>
      <li><svg width="11" height="11" viewBox="0 0 12 12"><path d="M2 0l3 3-1.5 1.5a7 7 0 0 0 4 4L9 7l3 3-2 2C5 12 0 7 0 2z" fill="#fff"/></svg>021-555-0142</li>
      <li><svg width="11" height="9" viewBox="0 0 12 9"><rect width="12" height="9" fill="#fff"/><polyline points="0,0 6,5 12,0" fill="none" stroke="#000"/></svg>hello@tasmaneride.example</li>
      <li><svg width="11" height="11" viewBox="0 0 12 12"><circle cx="6" cy="6" r="5.3" fill="none" stroke="#fff" stroke-width="1.2"/><ellipse cx="6" cy="6" rx="2.3" ry="5.3" fill="none" stroke="#fff"/><line x1="1" y1="6" x2="11" y2="6" stroke="#fff"/></svg>www.tasmaneride.example</li>
    </ul>
    <div class="quicklinks">
      <h5>QuickLinks</h5>
      <ul><li>About us</li><li>What we offer</li><li>Bookings/Contact</li></ul>
    </div>
  </div>

  <div class="footer-col booking">
    <h5>Booking</h5>
    <div class="field f1">First Name:</div>
    <div class="field f2">LastName :</div>
    <div class="field f3">Phone No :</div>
    <div class="field f4">Email Address :</div>
    <div class="field f5">Message :</div>
    <div class="submit">Submit</div>
  </div>
</footer>

<div class="footer-bar"><span>© 2017 tasmaneride</span>|<span>Privacy Policy</span>|<span>User Agreement</span></div>

</body>
</html>
```